Business card for law firm

Need business card for new law firm. Think confident, authoritative, conservative, but not stuffy or old-fashioned.

Contact Information for Business Card

Content for card - logo (uploaded), plus the following:

Paul Whitcombe (larger font)
Managing Partner (larger font, but not as large as name)
Level 9, 7 Ferris Lane
Sydney NSW 2000
Main Tel 02 9364 2710
Direct Tel 02 8472 3159
Email paul@qvlegal.com.au
www.qvlegal.com.au

Letterhead design should include logo plus:
Level 9, 7 Ferris Lane
Sydney NSW 2000
Tel 02 8472 3159
www.qvlegal.com.au

```html
<!DOCTYPE html>
<html lang="en">
<head>
<meta charset="utf-8">
<title>QV Legal — Business Card</title>
<link rel="stylesheet" href="https://fonts.googleapis.com/css2?family=Open+Sans:wght@400;600;700&display=swap">
<style>
  :root {
    --backdrop: #1e1f21;
    --card: #ffffff;
    --navy: #0f1f5c;
    --ink: #111111;
    --edge: #000000;
    --on-navy: #ffffff;
  }
  * { box-sizing: border-box; margin: 0; padding: 0; }
  html, body {
    width: 1200px; height: 960px; overflow: hidden;
    background: var(--backdrop);
    font-family: "Open Sans", Arial, sans-serif;
  }
  .canvas {
    width: 1200px; height: 960px;
    display: flex; flex-direction: column; align-items: center; justify-content: center;
    gap: 60px;
  }
  .card {
    position: relative;
    width: 700px; height: 400px;
    background: var(--card);
    overflow: hidden;
    box-shadow: 0 18px 40px rgba(0,0,0,.45);
  }

  /* Front */
  .front .brand {
    position: absolute; left: 0; right: 0; top: 140px;
    display: flex; align-items: center; justify-content: center; gap: 22px;
  }
  .brand-square { width: 52px; height: 52px; background: var(--navy); flex: none; }
  .brand-name {
    font-weight: 600; color: var(--ink); letter-spacing: 6px;
    text-transform: uppercase; line-height: 1;
  }
  .front .brand-name { font-size: 62px; }
  .front .site {
    position: absolute; left: 0; right: 0; top: 238px;
    text-align: center; font-size: 17px; letter-spacing: 3px; color: var(--ink);
  }

  /* Back */
  .back .brand {
    position: absolute; left: 48px; top: 150px;
    display: flex; align-items: center; gap: 14px;
  }
  .back .brand-square { width: 30px; height: 30px; }
  .back .brand-name { font-size: 38px; letter-spacing: 4px; }
  .back .disc { position: absolute; inset: 0; }
  .contact {
    position: absolute; left: 402px; top: 66px; width: 262px;
    color: var(--on-navy);
  }
  .contact .name { font-size: 23px; font-weight: 700; text-transform: uppercase; letter-spacing: .5px; }
  .contact .role { font-size: 15px; text-transform: uppercase; letter-spacing: .5px; margin-bottom: 16px; }
  .contact .address { font-size: 17px; line-height: 1.35; margin-bottom: 16px; }
  .contact ul { list-style: none; }
  .contact li {
    display: flex; justify-content: space-between; align-items: center;
    font-size: 16px; line-height: 1.7;
  }
  .contact li svg { width: 16px; height: 16px; flex: none; margin-left: 8px; }
</style>
</head>
<body>
<main class="canvas">

  <section class="card front" aria-label="Card front">
    <div class="brand">
      <span class="brand-square"></span>
      <span class="brand-name">QV Legal</span>
    </div>
    <p class="site">www.qvlegal.com.au</p>
  </section>

  <section class="card back" aria-label="Card back">
    <div class="brand">
      <span class="brand-square"></span>
      <span class="brand-name">QV Legal</span>
    </div>

    <svg class="disc" viewBox="0 0 700 400" aria-hidden="true">
      <circle cx="696" cy="212" r="372" fill="var(--edge)"/>
      <circle cx="712" cy="206" r="372" fill="var(--navy)"/>
    </svg>

    <div class="contact">
      <p class="name">Paul Whitcombe</p>
      <p class="role">Managing Partner</p>
      <p class="address">Level 9, 7 Ferris Lane<br>Sydney NSW 2000</p>
      <ul>
        <li>02 9364 2710 (Main)
          <svg viewBox="0 0 16 16"><circle cx="8" cy="8" r="7.5" fill="#fff"/><path d="M5 4.2l1.6-.4 1 2.2-1 .8a6 6 0 0 0 2.6 2.6l.8-1 2.2 1-.4 1.6c-3.6.3-7-3.2-6.8-6.8z" fill="var(--navy)"/></svg>
        </li>
        <li>02 8472 3159 (Direct)
          <svg viewBox="0 0 16 16"><circle cx="8" cy="8" r="7.5" fill="#fff"/><path d="M5 4.2l1.6-.4 1 2.2-1 .8a6 6 0 0 0 2.6 2.6l.8-1 2.2 1-.4 1.6c-3.6.3-7-3.2-6.8-6.8z" fill="var(--navy)"/></svg>
        </li>
        <li>paul@qvlegal.com.au
          <svg viewBox="0 0 16 16"><circle cx="8" cy="8" r="7.5" fill="#fff"/><rect x="4" y="5.2" width="8" height="5.6" fill="none" stroke="var(--navy)" stroke-width="1.2"/><path d="M4 5.4l4 3 4-3" fill="none" stroke="var(--navy)" stroke-width="1.2"/></svg>
        </li>
        <li>www.qvlegal.com.au
          <svg viewBox="0 0 16 16"><circle cx="8" cy="8" r="7.5" fill="#fff"/><g fill="none" stroke="var(--navy)" stroke-width="1"><circle cx="8" cy="8" r="4.5"/><ellipse cx="8" cy="8" rx="2" ry="4.5"/><path d="M3.5 8h9"/></g></svg>
        </li>
      </ul>
    </div>
  </section>

</main>
</body>
</html>
```